Anzeigengestaltung für Verkauf & Installation von Alarmanlagen und Videoüberwachungssystemen
Zielgruppe
Verkauf und Installation von Alarmanlagen und Videoüberwachungssystemen.
Verkauf erfolgt über eigenen Onlineshop.
Installation der Anlagen im regionalen Umkreis, hauptsächlich Privatkunden.
Zielgruppe: Privatkunden, Familien, mit vorhandener Immobilie/Wohneigentum.
Aufgabenstellung
Zeitungsformat:
92 mm x 60 mm
s/w-4C
Text Entwurf als Orientierung befindet sich im Anhang, ebenso das Firmenlogo.
Bilder aus der Webseite sind ebenfalls beigefügt. Vielleicht lässt sich damit etwas anfangen, ich bin aber auch für Vorschläge aus geeigneten Stock-Bildern offen.

```html
<!DOCTYPE html>
<html lang="de">
<head>
<meta charset="utf-8">
<title>Sicherheitshof – Anzeige</title>
<link href="https://fonts.googleapis.com/css2?family=Arimo:wght@400;700&family=Oswald:wght@500;600&display=swap" rel="stylesheet">
<style>
  :root {
    --page: #ffffff;
    --ad-light: #f1f1f1;
    --ad-mid: #e2e2e2;
    --brand-red: #d63b2f;
    --ink: #1e1e1e;
    --ink-soft: #444444;
    --photo-dark: #1c2b55;
    --photo-warm: #8a5a36;
    --photo-room: #d9cfc8;
    --photo-room-dark: #9c8780;
  }
  html, body {
    margin: 0;
    padding: 0;
    width: 1200px;
    height: 2400px;
    overflow: hidden;
    background: var(--page);
  }
  .canvas {
    position: relative;
    width: 1200px;
    height: 2400px;
  }
  .advert {
    position: absolute;
    left: 50px;
    top: 841px;
    width: 1100px;
    height: 717px;
    display: block;
  }
  .brand-name { font-family: "Arimo", Arial, sans-serif; font-weight: 700; fill: var(--ink-soft); }
  .headline { font-family: "Oswald", "Arial Narrow", sans-serif; font-weight: 600; fill: var(--brand-red); }
  .feature { font-family: "Arimo", Arial, sans-serif; font-weight: 400; fill: var(--ink); }
  .service-label { font-family: "Oswald", "Arial Narrow", sans-serif; font-weight: 500; fill: var(--ink); }
  .contact { font-family: "Arimo", Arial, sans-serif; font-weight: 400; fill: var(--ink); }
  .contact-dot { fill: var(--brand-red); }
</style>
</head>
<body>
<div class="canvas">
  <svg class="advert" viewBox="0 0 747 487" xmlns="http://www.w3.org/2000/svg">
    <defs>
      <linearGradient id="adBackground" x1="0" y1="0" x2="1" y2="1">
        <stop offset="0" stop-color="var(--ad-light)"/>
        <stop offset="0.45" stop-color="#f6f6f6"/>
        <stop offset="0.7" stop-color="var(--ad-mid)"/>
        <stop offset="1" stop-color="#ececec"/>
      </linearGradient>
      <linearGradient id="burglarTones" x1="0" y1="0" x2="1" y2="0">
        <stop offset="0" stop-color="#2b3f86"/>
        <stop offset="0.55" stop-color="var(--photo-dark)"/>
        <stop offset="1" stop-color="var(--photo-warm)"/>
      </linearGradient>
      <linearGradient id="phoneTones" x1="0" y1="0" x2="1" y2="1">
        <stop offset="0" stop-color="var(--photo-room)"/>
        <stop offset="0.6" stop-color="#efe9e4"/>
        <stop offset="1" stop-color="var(--photo-room-dark)"/>
      </linearGradient>
    </defs>

    <rect class="ad-ground" width="747" height="487" fill="url(#adBackground)"/>

    <g class="brand">
      <circle cx="55" cy="68" r="24" fill="var(--ink-soft)"/>
      <text class="brand-name" x="92" y="78" font-size="28">Sicherheitshof</text>
    </g>

    <text class="headline" x="28" y="171" font-size="27">MODERNE FUNKALARMANLAGEN</text>
    <g class="feature-list">
      <g transform="translate(38,200)">
        <circle r="8" fill="var(--ink)"/>
        <path d="M-3.5 0 L-1 2.8 L4 -2.8" stroke="#fff" stroke-width="2" fill="none"/>
      </g>
      <text class="feature" x="57" y="207" font-size="19">Individuelle Beratung</text>
      <g transform="translate(38,229)">
        <circle r="8" fill="var(--ink)"/>
        <path d="M-3.5 0 L-1 2.8 L4 -2.8" stroke="#fff" stroke-width="2" fill="none"/>
      </g>
      <text class="feature" x="57" y="236" font-size="19">Onlineshop</text>
      <g transform="translate(38,258)">
        <circle r="8" fill="var(--ink)"/>
        <path d="M-3.5 0 L-1 2.8 L4 -2.8" stroke="#fff" stroke-width="2" fill="none"/>
      </g>
      <text class="feature" x="57" y="265" font-size="19">Installation</text>
    </g>

    <text class="headline" x="27" y="331" font-size="26">BAUFONDS FÖRDERUNG MÖGLICH</text>

    <g class="services">
      <g class="icon-alarm" fill="none" stroke="var(--ink)" stroke-width="1.6">
        <rect x="30" y="352" width="26" height="20" rx="2"/>
        <rect x="34" y="356" width="7" height="4" fill="var(--ink)"/>
        <path d="M44 357h8M44 361h8M34 365h18M34 368h18"/>
        <rect x="48" y="346" width="8" height="6" fill="var(--brand-red)" stroke="none"/>
      </g>
      <text class="service-label" x="62" y="371" font-size="16">ALARM</text>

      <g class="icon-video" fill="none" stroke="var(--ink)" stroke-width="1.8">
        <path d="M122 355v-5h6M140 350h6v5M146 367v5h-6M128 372h-6v-5"/>
        <circle cx="134" cy="361" r="4" fill="var(--brand-red)" stroke="none"/>
      </g>
      <text class="service-label" x="152" y="371" font-size="16">VIDEO</text>

      <g class="icon-home" fill="none" stroke="var(--ink)" stroke-width="1.6">
        <path d="M200 362l10-10 10 10M203 360v11h6"/>
        <rect x="213" y="354" width="12" height="19" rx="2"/>
        <path d="M219 358l4 7h-8z" fill="var(--brand-red)" stroke="none"/>
      </g>
      <text class="service-label" x="241" y="371" font-size="16">HAUSAUTOMATION</text>
    </g>

    <g class="contact-block">
      <text class="contact" x="30" y="434" font-size="11.5">Lindenstieg 12</text>
      <circle class="contact-dot" cx="119" cy="430" r="3"/>
      <text class="contact" x="129" y="434" font-size="11.5">74899 Weilerbach</text>
      <circle class="contact-dot" cx="234" cy="430" r="3"/>
      <text class="contact" x="244" y="434" font-size="11.5">07955-3812</text>
      <text class="contact" x="30" y="455" font-size="11.5">www.sicherheitshof.de  E-Mail: info@sicherheitshof.de</text>
    </g>

    <polygon class="accent-band" points="432,140 578,0 595,0 449,140 735,440 745,440" fill="var(--brand-red)"/>
    <polygon class="burglar-photo" role="img" aria-label="Foto: maskierter Einbrecher hebelt mit einem Brecheisen ein Fenster auf"
             points="449,140 595,0 747,0 747,440 735,440" fill="url(#burglarTones)"/>

    <polygon class="accent-band" points="335,487 500,258 505,258 352,487" fill="var(--brand-red)"/>
    <polygon class="phone-photo" role="img" aria-label="Foto: Hand hält ein Smartphone mit Live-Bildern einer Überwachungskamera aus Wohnräumen"
             points="352,487 505,258 548,258 747,467 747,487" fill="url(#phoneTones)"/>
  </svg>
</div>
</body>
</html>
```